Brightfield Ventures Inc. Letterhead

Creation of attractive and eye catching letterhead for a business start-up for the construction industry. Letterhead must relate to construction, but avoid standard hammer and tools in the design.

I forgot to add some details, sorry about that. Some pertinent info: Ph: 916-555-0187 brightfieldventures.example 448 Willowmere Ave, Ste 210 Folsom, CA 95999 info@brightfieldventures.example not sure if slogan should be in there" “Connecting construction professionals to create a purpose driven industry.” must be able to be used in word. Thanks!

```html
<!DOCTYPE html>
<html lang="en">
<head>
<meta charset="utf-8">
<title>Brightfield Ventures Inc. Letterhead</title>
<link rel="stylesheet" href="https://fonts.googleapis.com/css2?family=Lato:wght@400;700&family=Yellowtail&display=swap">
<style>
  :root {
    --navy: #1b1f50;
    --red: #c8232c;
    --ink: #4a4a4f;
    --paper: #ffffff;
    --backdrop: #e4e4e6;
  }
  * { margin: 0; padding: 0; box-sizing: border-box; }
  html, body { width: 946px; height: 1200px; overflow: hidden; background: var(--backdrop); }
  .letterhead {
    position: relative;
    width: 946px;
    height: 1200px;
    background: var(--paper);
    font-family: "Lato", sans-serif;
    color: var(--ink);
  }
  .header-band {
    position: absolute; left: 0; top: 0;
    width: 100%; height: 74px;
    background: var(--navy);
  }
  .header-rule {
    position: absolute; left: 0; top: 78px;
    width: 100%; height: 3px;
    background: var(--red);
  }
  .brand {
    position: absolute; left: 0; top: 118px;
    width: 100%;
    display: flex; justify-content: center; align-items: center; gap: 12px;
  }
  .brand-mark { width: 16px; height: 16px; background: var(--red); }
  .brand-name {
    font-family: "Lato", sans-serif;
    font-weight: 700;
    font-size: 22px;
    letter-spacing: 2.5px;
    text-transform: uppercase;
    color: var(--navy);
  }
  .letter-body {
    position: absolute; left: 81px; top: 316px;
    width: 785px;
  }
  .salutation {
    font-weight: 700; font-size: 17px; color: var(--navy);
    margin-bottom: 18px;
  }
  .letter-body p.paragraph {
    font-size: 16.6px; line-height: 27.5px;
    margin-bottom: 20px;
  }
  .closing { margin-top: 26px; font-size: 20px; color: #222; }
  .signature {
    font-family: "Yellowtail", cursive;
    font-size: 36px; color: var(--navy);
    margin-top: 2px;
  }
  .footer {
    position: absolute; left: 0; top: 1142px; width: 100%;
    text-align: center; font-size: 13.5px; color: var(--ink);
  }
  .footer-line { display: flex; justify-content: center; gap: 14px; align-items: center; line-height: 22px; }
  .contact-item { display: inline-flex; align-items: center; gap: 4px; }
  .contact-item svg { width: 11px; height: 11px; fill: var(--red); }
</style>
</head>
<body>
<main class="letterhead">
  <div class="header-band"></div>
  <div class="header-rule"></div>

  <div class="brand">
    <span class="brand-mark"></span>
    <span class="brand-name">Brightfield Ventures</span>
  </div>

  <section class="letter-body">
    <p class="salutation">Dear Mr. Lorem,</p>
    <p class="paragraph">Lorem ipsum dolor sit amet, consectetuer adipiscing elit, sed diam nonummy nibh euismod tincidunt ut laoreet dolore magna aliquam erat volutpat. Ut wisi enim ad minim veniam, quis nostrud exerci tation ullamcorper suscipit lobortis nisl ut aliquip ex ea commodo consequat. Duis autem vel eum iriure dolor in hendiusto odio dignissim qui blandit praesent luptatum zzril delenit augue duis dolore te feugait nulla facilisi.</p>
    <p class="paragraph">Lorem ipsum dolor sit amet, consectetuer adipiscing elit, sed diam nonummy nibh euismod tincidunt ut laoreet dolore magna aliquam erat volutpat. Ut wisi enim ad minim veniam, quis nostrud exerci tation ullamcorper suscipit lobortis nisl ut aliquip ex ea commodo consequat. Duis autem vel eum iriure dolor in hendiusto odio dignissim qui blandit praesent luptatum zzril delenit augue duis dolore te feugait nulla facilisi.</p>
    <p class="paragraph">Lorem ipsum dolor sit amet, consectetuer adipiscing elit, sed diam nonummy nibh euismod tincidunt ut laoreet dolore magna aliquam erat volutpat. Ut wisi enim ad minim veniam, quis nostrud exerci tation ullamcorper suscipit lobortis nisl ut aliquip ex ea commodo consequat. Duis autem vel eum iriure dolor in hendiusto odio dignissim qui blandit praesent luptatum zzril delenit augue duis dolore te feugait nulla facilisi.</p>
    <p class="closing">Sincerely Your,</p>
    <p class="signature">Your Name</p>
  </section>

  <footer class="footer">
    <div class="footer-line">
      <span class="contact-item">
        <svg viewBox="0 0 12 12" aria-hidden="true"><path d="M6 0a4.2 4.2 0 0 0-4.2 4.2C1.8 7.4 6 12 6 12s4.2-4.6 4.2-7.8A4.2 4.2 0 0 0 6 0zm0 6a1.8 1.8 0 1 1 0-3.6A1.8 1.8 0 0 1 6 6z"/></svg>
        448 Willowmere Ave, Ste 210, Folsom, CA 95999
      </span>
    </div>
    <div class="footer-line">
      <span class="contact-item">
        <svg viewBox="0 0 12 12" aria-hidden="true"><path d="M2.4 0.6 4.2 2.8 3.2 4.4a7 7 0 0 0 4.4 4.4l1.6-1 2.2 1.8-1.2 1.8C5.4 11.6 0.4 6.6 0.6 1.8z"/></svg>
        916-555-0187
      </span>
      <span class="contact-item">
        <svg viewBox="0 0 12 12" aria-hidden="true"><path d="M0 2h12v8H0zM1 3l5 3.6L11 3v-.2H1z"/></svg>
        info@brightfieldventures.example
      </span>
      <span class="contact-item">
        <svg viewBox="0 0 12 12" aria-hidden="true"><circle cx="6" cy="6" r="6"/></svg>
        www.brightfieldventures.example
      </span>
    </div>
  </footer>
</main>
</body>
</html>
```